Corporate Business Card

Very professional, Modern, Not to busy, include phone address email, website
(555) 617-4930, 18761 52nd Avenue S, Cedarmoor, OR 98047, martin@plumlinegroup.com, varkoworks.com

Target Market(s)

Manufacturing

Industry/Entity Type

Aero, machining, manufacturing, Off road racing

Contact Information for Business Card

Phone, address email, website

```html
<!DOCTYPE html>
<html lang="en">
<head>
<meta charset="utf-8">
<title>Varko Works – Business Card</title>
<link rel="stylesheet" href="https://fonts.googleapis.com/css2?family=Arimo:wght@400;700&display=swap">
<style>
  :root {
    --bg: #e4e4e2;
    --navy: #22366b;
    --navy-light: #2c4174;
    --red: #d3171e;
    --white: #ffffff;
  }
  * { margin: 0; padding: 0; box-sizing: border-box; }
  html, body { width: 1200px; height: 801px; overflow: hidden; }
  body {
    background: var(--bg);
    font-family: "Arimo", Arial, sans-serif;
    position: relative;
  }
  .card {
    position: absolute;
    top: 246px;
    width: 540px;
    height: 309px;
    background: var(--navy);
    overflow: hidden;
    box-shadow: 0 6px 18px rgba(0,0,0,0.18);
  }
  .card-front { left: 40px; }
  .card-back { left: 620px; }

  .panel { position: absolute; background: var(--navy-light); }
  .panel-contact { left: 24px; top: 150px; width: 300px; height: 130px; border-radius: 28px 0 0 28px; }
  .panel-upper { left: 300px; top: 0; width: 150px; height: 150px; }
  .panel-right { left: 420px; top: 40px; width: 120px; height: 200px; }

  .brand {
    position: absolute;
    left: 34px;
    top: 42px;
    display: flex;
    align-items: center;
    gap: 10px;
    color: var(--white);
    font-weight: 700;
    font-size: 34px;
    letter-spacing: 1px;
  }
  .brand-mark { width: 16px; height: 16px; background: var(--red); }
  .brand-rule {
    position: absolute;
    left: 34px; top: 100px;
    width: 170px; height: 2px;
    background: var(--white);
  }

  .person { position: absolute; left: 56px; top: 170px; }
  .person-name {
    color: var(--red);
    font-size: 17px;
    letter-spacing: 0.5px;
    text-transform: uppercase;
  }
  .person-title { color: var(--white); font-size: 13px; margin-top: 2px; }

  .contact-list {
    position: absolute;
    left: 56px; top: 222px;
    list-style: none;
    color: var(--white);
    font-size: 12.5px;
  }
  .contact-list li { display: flex; align-items: center; gap: 9px; height: 18px; }
  .contact-list svg { width: 12px; height: 12px; fill: var(--red); flex: none; }

  .address {
    position: absolute;
    right: 26px; top: 150px;
    color: var(--white);
    font-size: 13px;
    text-align: right;
    line-height: 1.45;
  }

  .tab-accent {
    position: absolute;
    left: 0; top: 166px;
    width: 10px; height: 34px;
    background: var(--red);
    border-radius: 0 4px 4px 0;
  }
  .edge-band {
    position: absolute;
    bottom: 0; left: 0;
    width: 100%; height: 8px;
    display: flex;
  }
  .edge-band-red { flex: 0 0 58%; background: var(--red); }
  .edge-band-white { flex: 1; background: var(--white); }

  .back-texture {
    position: absolute; inset: 0;
    background: radial-gradient(circle at 50% 50%, #26396f 0%, var(--navy) 70%);
  }
  .back-brand {
    position: absolute;
    left: 0; right: 0; top: 118px;
    display: flex; justify-content: center; align-items: center; gap: 12px;
    color: var(--white);
    font-weight: 700;
    font-size: 40px;
    letter-spacing: 1px;
  }
  .back-brand .brand-mark { width: 18px; height: 18px; }
  .back-rule {
    position: absolute;
    left: 120px; top: 180px;
    width: 180px; height: 2px;
    background: var(--white);
  }
</style>
</head>
<body>
  <section class="card card-front" aria-label="Business card front">
    <div class="panel panel-upper"></div>
    <div class="panel panel-right"></div>
    <div class="panel panel-contact"></div>

    <div class="brand"><span class="brand-mark"></span>VARKO WORKS</div>
    <div class="brand-rule"></div>

    <div class="tab-accent"></div>
    <div class="person">
      <p class="person-name">Daniel Reeves</p>
      <p class="person-title">Manager</p>
    </div>

    <ul class="contact-list">
      <li>
        <svg viewBox="0 0 24 24" aria-hidden="true"><path d="M6.6 10.8a15.1 15.1 0 0 0 6.6 6.6l2.2-2.2a1 1 0 0 1 1-.25 11.4 11.4 0 0 0 3.6.57 1 1 0 0 1 1 1V20a1 1 0 0 1-1 1A17 17 0 0 1 3 4a1 1 0 0 1 1-1h3.5a1 1 0 0 1 1 1c0 1.25.2 2.45.57 3.57a1 1 0 0 1-.25 1z"/></svg>
        (555) 617-4930
      </li>
      <li>
        <svg viewBox="0 0 24 24" aria-hidden="true"><path d="M2 5h20v14H2z M2 5l10 8 10-8" stroke="#22366b" stroke-width="1.5"/></svg>
        martin@plumlinegroup.com
      </li>
      <li>
        <svg viewBox="0 0 24 24" aria-hidden="true"><circle cx="12" cy="12" r="10"/><path d="M2 12h20M12 2c3 3 3 17 0 20M12 2c-3 3-3 17 0 20" stroke="#22366b" stroke-width="1.5" fill="none"/></svg>
        www.varkoworks.com
      </li>
    </ul>

    <p class="address">18761 52nd Avenue S<br>Cedarmoor, OR 98047</p>

    <div class="edge-band">
      <span class="edge-band-red"></span>
      <span class="edge-band-white"></span>
    </div>
  </section>

  <section class="card card-back" aria-label="Business card back">
    <div class="back-texture" role="img" aria-label="Faint embossed brand-name pattern across the card"></div>
    <div class="back-brand"><span class="brand-mark"></span>VARKO WORKS</div>
    <div class="back-rule"></div>
  </section>
</body>
</html>
```